KRWB new business card design

We need a business card design for our established business which is Australia wide however based in Melbourne. We are a young team of Financial Planners who specialize in Insurance and Basic super advice for people like us.

We are people who help our clients get things done in a timely and cost effective manner whilst having a good time and a laugh along the way.

We would like this to have a consistent feel with our new e-brochure which i have attached from a color and font perspective.

Industry/Entity Type

Business

Requirements
Must have
• We do not need specific address details rather just the states we are in:

VIC/NSW/QLD/TAS
Nice to have
• Curved edge to mate the brochure

```html
<!DOCTYPE html>
<html lang="en">
<head>
<meta charset="utf-8">
<title>KRWB Planning – Business Card Set</title>
<link href="https://fonts.googleapis.com/css2?family=Arimo:ital,wght@0,400;0,700;1,700&family=PT+Sans&display=swap" rel="stylesheet">
<style>
  :root {
    --stage: #e9e6e1;
    --label: #2b2b2b;
    --card-dark: #0c0c0c;
    --card-dark-glow: #3a3a3a;
    --mesh-dark: #1b1b1b;
    --mesh-mid: #2c2c2c;
    --white: #ffffff;
    --green: #6cbf4b;
    --green-deep: #0fa04a;
    --grey-text: #7a7a7a;
    --dark-text: #3a3a3a;
    --rule: #bdbdbd;
  }
  * { box-sizing: border-box; margin: 0; padding: 0; }
  html, body { width: 1200px; height: 788px; overflow: hidden; }
  body {
    position: relative;
    background: var(--stage);
    font-family: "Arimo", Arial, sans-serif;
  }
  .view-label {
    position: absolute;
    width: 525px;
    text-align: center;
    font-family: "PT Sans", sans-serif;
    font-size: 22px;
    color: var(--label);
  }
  .card {
    position: absolute;
    width: 525px;
    height: 300px;
    border-radius: 22px;
    overflow: hidden;
    box-shadow: 0 4px 14px rgba(0,0,0,.28);
  }
  .card--front {
    left: 54px; top: 75px;
    background: radial-gradient(circle at 52% 45%, var(--card-dark-glow) 0%, var(--card-dark) 60%);
    color: var(--white);
  }
  .card--back-one { left: 622px; top: 75px; height: 298px; background: var(--white); }
  .card--back-two { left: 54px; top: 446px; height: 298px; background: var(--white); }
  .card--back-three {
    left: 622px; top: 446px;
    background: radial-gradient(circle at 30% 45%, var(--mesh-mid) 0%, var(--mesh-dark) 70%);
    color: var(--white);
  }
  .abs { position: absolute; }
  .brand-name {
    font-weight: 700;
    white-space: nowrap;
    line-height: 1;
  }
  .brand-mark {
    display: inline-block;
    width: 14px; height: 14px;
    background: var(--green);
    margin-left: 10px;
    vertical-align: middle;
  }
  /* front */
  .front-brand { left: 46px; top: 24px; font-size: 40px; color: var(--white); }
  .adviser-name { left: 42px; top: 102px; font-size: 17px; font-weight: 700; }
  .adviser-role { left: 42px; top: 122px; font-size: 12.5px; font-weight: 700; }
  .front-rule { left: 36px; top: 143px; width: 276px; height: 1px; background: #8a8a8a; }
  .front-stem { left: 36px; top: 143px; width: 1px; height: 140px; background: #8a8a8a; }
  .contact-list { left: 28px; top: 150px; list-style: none; }
  .contact-list li {
    display: flex; align-items: center;
    height: 22px; font-size: 13.5px;
  }
  .contact-list svg { width: 10px; height: 10px; margin-right: 6px; fill: var(--green); }
  /* lists */
  .speciality-title { font-size: 18px; font-weight: 700; font-style: italic; }
  .speciality-list { list-style: none; }
  .speciality-list li { font-size: 14px; font-weight: 700; height: 34px; line-height: 34px; }
  .speciality-list li::before { content: "\25AA\00A0"; }
  .back-one-brand { left: 0; width: 260px; top: 200px; text-align: center; font-size: 28px; color: #1a1a1a; }
  .back-one-divider { left: 260px; top: 20px; width: 2px; height: 236px;
    background: linear-gradient(to bottom, transparent, var(--rule) 40%, #777 60%, transparent); }
  .back-one-list { left: 320px; top: 44px; color: var(--grey-text); }
  .back-one-list .speciality-list { margin-top: 6px; }
  .tagline-band {
    left: 0; bottom: 0; width: 100%; height: 38px;
    background: var(--green); color: var(--white);
    font-size: 14px; font-weight: 700; text-align: center; line-height: 38px;
  }
  .back-two-list { left: 0; width: 100%; top: 44px; text-align: center; color: var(--dark-text); }
  .back-two-list .speciality-list { margin-top: 6px; }
  .back-two-tagline { left: 0; width: 100%; top: 268px; text-align: center; font-size: 14px; font-weight: 700; color: var(--dark-text); }
  .back-three-brand { left: 0; width: 300px; top: 230px; text-align: center; font-size: 34px; color: var(--white); }
  .back-three-list { left: 313px; top: 23px; }
  .back-three-list .speciality-list { margin-top: 6px; }
  .back-three-tagline { left: 313px; top: 252px; font-size: 14px; font-weight: 700; color: var(--green); line-height: 18px; }
</style>
</head>
<body>
  <div class="view-label" style="left:54px; top:33px;">Front</div>
  <div class="view-label" style="left:622px; top:33px;">Back - 1</div>
  <div class="view-label" style="left:54px; top:404px;">Back - 2</div>
  <div class="view-label" style="left:622px; top:404px;">Back - 3</div>

  <section class="card card--front">
    <div class="abs brand-name front-brand">KRWB Planning<span class="brand-mark"></span></div>
    <div class="abs adviser-name">Martin Holloway</div>
    <div class="abs adviser-role">ADFS, BBus, LRS© - Financial Adviser</div>
    <div class="abs front-rule"></div>
    <div class="abs front-stem"></div>
    <ul class="abs contact-list">
      <li><svg viewBox="0 0 10 10"><path d="M2 1l2 2-1 1.5a5 5 0 0 0 2.5 2.5L7 6l2 2-1.5 1.5C4 9 1 6 .5 2.5z"/></svg>1300 555 014</li>
      <li><svg viewBox="0 0 10 10"><rect x="1" y="3" width="8" height="5" rx="1"/><rect x="3" y="1" width="4" height="2"/></svg>03 9555 0182</li>
      <li><svg viewBox="0 0 10 10"><rect x="2.5" y="0.5" width="5" height="9" rx="1"/></svg>0400 555 276</li>
      <li><svg viewBox="0 0 10 10"><rect x="0.5" y="2" width="9" height="6" rx="1"/></svg>martin@krwb.com.au</li>
      <li><svg viewBox="0 0 10 10"><circle cx="5" cy="5" r="4.5"/></svg>www.krwb.com.au</li>
      <li>VIC/NSW/QLD/TAS</li>
    </ul>
  </section>

  <section class="card card--back-one">
    <div class="abs brand-name back-one-brand">KRWB Planning</div>
    <div class="abs back-one-divider"></div>
    <div class="abs back-one-list">
      <div class="speciality-title">Specialising in</div>
      <ul class="speciality-list">
        <li>Risk Insurance</li>
        <li>Debt Management</li>
        <li>Superannuation</li>
        <li>Wealth Creation</li>
        <li>Retirement Planning</li>
      </ul>
    </div>
    <div class="abs tagline-band">SECURE FUTURE, ENHANCED LIFESTYLE</div>
  </section>

  <section class="card card--back-two">
    <div class="abs back-two-list">
      <div class="speciality-title">Specialising in</div>
      <ul class="speciality-list">
        <li>Risk Insurance</li>
        <li>Debt Management</li>
        <li>Superannuation</li>
        <li>Wealth Creation</li>
        <li>Retirement Planning</li>
      </ul>
    </div>
    <div class="abs back-two-tagline">SECURE FUTURE, ENHANCED LIFESTYLE</div>
  </section>

  <section class="card card--back-three">
    <div class="abs brand-name back-three-brand">KRWB Planning</div>
    <div class="abs back-three-list">
      <div class="speciality-title">Specialising in</div>
      <ul class="speciality-list">
        <li>Risk Insurance</li>
        <li>Debt Management</li>
        <li>Superannuation</li>
        <li>Wealth Creation</li>
        <li>Retirement Planning</li>
      </ul>
    </div>
    <div class="abs back-three-tagline">SECURE FUTURE<br>ENHANCED LIFESTYLE</div>
  </section>
</body>
</html>
```